VENTURE CAPITAL GROUP BUSINESS CARD DESIGN

Venture Capital Group based in SF looking for a bold business card design. No trendy colour explosion, 3D effects etc. Just "simple" optical effects. Works on your brain, keeps your eye focused and sticks to your mind.
Target Market(s)
Technology startups
Industry/Entity Type
Venture Capital
Contact Information for Business Card
DESMOND WHITLAKE
MANAGING PARTNER
187 FENWORTH ST SAN FRANCISCO, CA 94187
415.555.0142 O
415.555.0147 F
415.555.0193 C
desmond@veldtmoorcapital.ventures

```html
<!DOCTYPE html>
<html lang="en">
<head>
<meta charset="utf-8">
<title>Veldtmoor Capital Group – Business Card</title>
<link rel="stylesheet" href="https://fonts.googleapis.com/css2?family=Open+Sans:wght@400;600;700&display=swap">
<style>
  :root {
    --backdrop: #3a3431;
    --green-light: #52b548;
    --green-mid: #2f9a3c;
    --green-dark: #0e6a2b;
    --card-white: #ffffff;
    --ink-white: #ffffff;
    --ink-soft: #e8f5e9;
    --brand-green: #1f8a3a;
  }
  * { box-sizing: border-box; margin: 0; padding: 0; }
  html, body {
    width: 1200px; height: 844px; overflow: hidden;
    background: var(--backdrop);
    font-family: "Open Sans", Arial, sans-serif;
  }
  .canvas {
    position: relative; width: 1200px; height: 844px;
    display: flex; align-items: center; justify-content: center; gap: 44px;
  }
  .card {
    width: 520px; height: 300px; position: relative;
    box-shadow: 0 10px 24px rgba(0,0,0,.45);
  }
  .card--back {
    background: linear-gradient(200deg, var(--green-light) 0%, var(--green-mid) 45%, var(--green-dark) 100%);
    color: var(--ink-white);
  }
  .contact {
    position: absolute; right: 30px; top: 26px; text-align: right;
    font-size: 12.5px; line-height: 1.45; color: var(--ink-soft);
  }
  .contact__name { font-size: 16px; font-weight: 700; color: var(--ink-white); }
  .contact__title { margin-bottom: 12px; }
  .contact__address { margin-bottom: 4px; }
  .contact__line { display: flex; justify-content: flex-end; align-items: center; gap: 7px; }
  .contact__line svg { width: 11px; height: 11px; fill: var(--ink-white); }
  .contact__email {
    position: absolute; right: 30px; top: 192px; font-size: 13px; color: var(--ink-white);
  }
  .brand-name {
    font-family: "Open Sans", Arial, sans-serif; font-weight: 600;
    letter-spacing: 1px; white-space: nowrap;
  }
  .card--back .brand-name {
    position: absolute; right: 30px; bottom: 42px; font-size: 27px; color: var(--ink-white);
  }
  .card--front {
    background: var(--card-white);
    display: flex; align-items: center; justify-content: center;
  }
  .card--front .brand-name { font-size: 28px; color: var(--brand-green); }
</style>
</head>
<body>
<main class="canvas">
  <section class="card card--back" aria-label="Business card, contact side">
    <div class="contact">
      <div class="contact__name">Desmond Whitlake</div>
      <div class="contact__title">Managing Partner</div>
      <div class="contact__address">187 Fenworth St<br>San Francisco, CA 94187</div>
      <div class="contact__line">415.555.0142
        <svg viewBox="0 0 16 16" aria-label="office"><path d="M3 1l3 3-2 2c1 2 3 4 5 5l2-2 3 3-2 3C7 15 1 9 0 4z"/></svg></div>
      <div class="contact__line">415.555.0147
        <svg viewBox="0 0 16 16" aria-label="fax"><path d="M4 1h8v4h3v9H1V5h3zm1 1v3h6V2zM3 8v2h10V8z"/></svg></div>
      <div class="contact__line">415.555.0193
        <svg viewBox="0 0 16 16" aria-label="mobile"><path d="M4 0h8v16H4zm1 2v10h6V2z"/></svg></div>
    </div>
    <div class="contact__email">desmond@veldtmoorcapital.ventures</div>
    <div class="brand-name">VELDTMOOR CAPITAL GROUP</div>
  </section>

  <section class="card card--front" aria-label="Business card, brand side">
    <div class="brand-name">VELDTMOOR CAPITAL GROUP</div>
  </section>
</main>
</body>
</html>
```